New Payments Start-up requires Logo, Style Guide and Web Site Design

We need a logo, style guide (colour templates etc.) and marketing web-site (HTML/CSS styling) for Fenwu, a new account-to-account payment product for use in the Single European Payment Area (SEPA).

The design is for the product only, not a company brand. We're looking for basic palette and style guidelines also. The web site need only be a basic responsive cross-platform design and layout. We will produce our own content.

We have no requirements for specific colours or logo styles. It is a financial product, however, so should not appear too quirky or untrustworthy.

The product is still in the early phases of development, so we're not able to provide pictures or other content.

As a little more detail on how things work, though, our end customers will arrive at our site through redirection from our merchant partners (a number of whom are large multi-national companies) who have offered our services as an alternative to credit card payments. They will be able to set up a SEPA direct debit mandate online in just a few pages, secure that with a password and use it to pay both immediately and in future with a simple confirmation of the password… a quick, easy checkout.

Because we work with large customer in the payments space, whilst we’d like the brand to be modern and appealing, it has to engender trust and stability. Whilst this product is new and in start-up phase, our company has been in alternative payments for nearly 10 years and have strong products in Europe in the Pre-Paid Zelo/TrevinCard and Voucher space. We'd like to treat this separately, however, which is why we've briefed accordingly.

Reason: Apologies for the extension, but I had a couple of designers contact me to say they had completed work but were unable to submit because time ran out. I'll only extend this once, though, because we need to get cracking on the project. Many thanks Jem

Target Market(s)

European alternative payment customers

Industry/Entity Type

Financial

Logo Text

fenwu

Coding

Coded - Design and coding required

Number of Pages Required

1 page

Font styles to use
Sans Serif

```html
<!DOCTYPE html>
<html lang="en">
<head>
<meta charset="utf-8">
<title>Fenwu – Account-to-account payment</title>
<link href="https://fonts.googleapis.com/css2?family=Raleway:wght@300;400;500;600&family=Open+Sans:wght@400;600&display=swap" rel="stylesheet">
<style>
:root{
  --cyan:#1fb8d3;
  --yellow:#fdb913;
  --ink:#2b2b2b;
  --text:#555;
  --muted:#8a8a8a;
  --light:#f2f2f2;
  --white:#fff;
  --bar:#333333;
  --foot:#1b1b1b;
  --head:'Raleway',sans-serif;
  --body:'Open Sans',sans-serif;
}
*{margin:0;padding:0;box-sizing:border-box}
html,body{width:1200px;height:2609px;overflow:hidden;background:var(--white)}
body{position:relative;font-family:var(--body);color:var(--text)}
.abs{position:absolute}
a{color:inherit;text-decoration:none}

/* header */
.site-header{left:0;top:0;width:1200px;height:82px;background:var(--white)}
.logo{left:183px;top:12px;font-family:var(--head);font-weight:400;font-size:46px;color:#111;letter-spacing:1px}
.main-nav{left:473px;top:32px;display:flex;gap:32px;font-family:var(--head);font-size:16px;color:#666}

/* hero */
.hero{left:0;top:82px;width:1200px;height:457px;background:
  radial-gradient(ellipse 260px 200px at 560px 60px,rgba(150,110,85,.55),rgba(150,110,85,0) 70%),
  radial-gradient(ellipse 330px 260px at 480px 330px,rgba(255,255,255,.95),rgba(255,255,255,0) 70%),
  radial-gradient(ellipse 300px 200px at 900px 360px,rgba(255,255,255,.95),rgba(255,255,255,0) 70%),
  radial-gradient(ellipse 260px 300px at 80px 360px,rgba(205,190,170,.9),rgba(205,190,170,0) 70%),
  linear-gradient(100deg,#d9d3cb 0%,#cfc6ba 30%,#e3ddd5 60%,#eef0f2 100%)}
.hero-box{left:153px;top:154px;width:456px;height:166px;background:var(--cyan);color:var(--white);padding:22px 28px}
.hero-box .kicker{font-family:var(--head);font-weight:400;font-size:22px}
.hero-box h1{font-family:var(--head);font-weight:500;font-size:27px;margin-top:4px}
.hero-box p{font-size:12px;line-height:18px;margin-top:8px;opacity:.95}
.dots{left:563px;top:419px;display:flex;gap:6px}
.dots span{width:13px;height:13px;border-radius:50%;background:var(--white);border:2px solid #fff}
.dots span.on{background:#222}

/* cta band */
.cta-band{left:0;top:539px;width:1200px;height:87px;background:linear-gradient(#fafafa,#eeeeee);border-bottom:1px solid #ddd}
.cta-band p{left:217px;top:30px;font-family:var(--head);font-size:21px;color:#444}
.btn-yellow{left:847px;top:26px;width:129px;height:34px;background:var(--yellow);color:var(--white);font-family:var(--head);font-weight:600;font-size:13px;display:flex;align-items:center;justify-content:center;letter-spacing:.5px}

/* transfers */
.transfers{left:0;top:626px;width:1200px;height:344px}
.transfers h2{left:191px;top:57px;font-family:var(--head);font-weight:400;font-size:31px;color:var(--ink)}
.transfers .sub{left:192px;top:101px;font-family:var(--head);font-size:19px;color:#444}
.transfers .copy{left:192px;top:138px;width:450px;font-size:10.4px;line-height:18px;color:#777}
.btn-outline{font-family:var(--head);font-size:12px;height:34px;display:flex;align-items:center;justify-content:center;border:2px solid #999;color:#555}
.transfers .btn-outline{left:192px;top:228px;width:118px}
.transfers .illus{left:670px;top:31px;width:366px;height:265px;background:
  radial-gradient(ellipse 90px 60px at 200px 60px,rgba(90,180,230,.55),rgba(90,180,230,0) 75%),
  radial-gradient(ellipse 110px 50px at 160px 200px,rgba(236,110,120,.5),rgba(236,110,120,0) 75%),
  radial-gradient(ellipse 70px 60px at 50px 100px,rgba(200,200,205,.7),rgba(200,200,205,0) 75%),
  radial-gradient(ellipse 70px 60px at 300px 150px,rgba(200,200,205,.7),rgba(200,200,205,0) 75%),
  #fbfbfb}

/* features */
.features{left:0;top:970px;width:1200px;height:308px;background:var(--light)}
.feature{top:44px;width:260px;text-align:center}
.feature .icon{display:block;margin:0 auto}
.feature h3{font-family:var(--head);font-weight:400;font-size:19px;color:#333;margin-top:36px}
.feature p{font-size:11px;line-height:18px;color:#888;margin-top:10px;padding:0 20px}

/* split */
.split-photo{left:0;top:1278px;width:600px;height:400px;background:
  radial-gradient(ellipse 150px 110px at 430px 140px,rgba(205,200,195,.9),rgba(205,200,195,0) 70%),
  radial-gradient(ellipse 140px 60px at 250px 330px,rgba(150,165,185,.7),rgba(150,165,185,0) 70%),
  radial-gradient(ellipse 80px 120px at 40px 200px,rgba(120,160,80,.45),rgba(120,160,80,0) 70%),
  radial-gradient(ellipse 300px 80px at 300px 370px,rgba(215,205,190,.9),rgba(215,205,190,0) 70%),
  linear-gradient(120deg,#f3f0ea 0%,#ece6dd 50%,#e2dbd1 100%)}
.split-panel{left:600px;top:1278px;width:600px;height:400px;background:var(--cyan);color:var(--white)}
.split-panel h2{left:38px;top:82px;font-family:var(--head);font-weight:400;font-size:30px}
.split-panel .sub{left:38px;top:123px;font-family:var(--head);font-size:19px}
.split-panel .copy{left:38px;top:164px;width:370px;font-size:11px;line-height:18px}
.split-panel .btn-outline{left:38px;top:276px;width:118px;border-color:var(--white);color:var(--white)}

/* clients */
.clients{left:0;top:1678px;width:1200px;height:258px}
.clients h2{left:0;top:55px;width:1200px;text-align:center;font-family:var(--head);font-weight:400;font-size:21px;color:#666}
.client-row{left:232px;top:128px;width:770px;display:flex;justify-content:space-between;align-items:center}
.client{display:flex;align-items:center;gap:8px;font-family:var(--head);font-weight:600;font-size:22px;color:#8f8f8f}
.client i{display:block;width:18px;height:18px;background:#a5a5a5}
.client i.round{border-radius:50%}

/* promo panels */
.promo{top:1936px;height:328px;width:600px;color:var(--white);text-align:center}
.promo-how{left:0;background:
  radial-gradient(ellipse 180px 110px at 260px 170px,rgba(60,65,75,.55),rgba(60,65,75,0) 70%),
  linear-gradient(120deg,#9a9da2 0%,#7b7f86 50%,#9b9ea2 100%)}
.promo-help{left:593px;width:607px;background:
  radial-gradient(ellipse 220px 140px at 420px 200px,rgba(255,215,80,.7),rgba(255,215,80,0) 70%),
  linear-gradient(120deg,#f6c21a 0%,#f3b80e 60%,#f6c93a 100%)}
.promo h2{margin-top:118px;font-family:var(--head);font-weight:400;font-size:28px}
.promo p{width:400px;margin:10px auto 0;font-size:12px;line-height:19px}
.promo .btn-outline{width:118px;margin:14px auto 0;border-color:var(--white);color:var(--white)}

/* contact bar */
.contact-bar{left:0;top:2264px;width:1200px;height:66px;background:var(--bar);color:#eee;font-size:12px}
.contact-bar .item{top:24px;display:flex;align-items:center;gap:8px}

/* footer */
.site-footer{left:0;top:2330px;width:1200px;height:279px;background:var(--foot);color:#ddd}
.foot-col{top:44px}
.foot-col h4{font-family:var(--head);font-weight:500;font-size:13px;letter-spacing:.5px;color:#eee}
.foot-col ul{list-style:none;margin-top:14px}
.foot-col li{font-size:11px;line-height:25px;color:#ccc}
.foot-rule{left:195px;top:218px;width:830px;height:1px;background:#333}
.copyright{left:197px;top:240px;font-size:10px;color:#bbb}
.social{left:909px;top:235px;display:flex;gap:6px}
.social span{width:26px;height:26px;border:2px solid #ddd;border-radius:50%}
</style>
</head>
<body>

<header class="site-header abs">
  <div class="logo abs">Fenwu</div>
  <nav class="main-nav abs">
    <a>About Us</a><a>Checking</a><a>eBanking</a><a>Rates</a><a>Savings</a><a>Support</a>
  </nav>
</header>

<section class="hero abs" role="img" aria-label="Photo of a smiling man using a laptop on a sofa">
  <div class="hero-box abs">
    <div class="kicker">Account-to-account payment</div>
    <h1>Single European Payment Area</h1>
    <p>Ut nisi erat fermentum vel congue id euismod in elit Fusce ultricies orci ac feugiat suscipit leo massa sodales velit et</p>
  </div>
  <div class="dots abs"><span></span><span></span><span class="on"></span></div>
</section>

<section class="cta-band abs">
  <p class="abs">Fusce ultricies orci ac feugiat suscipit leo massa sodales velit</p>
  <a class="btn-yellow abs">GET STARTED</a>
</section>

<section class="transfers abs">
  <h2 class="abs">Account-to-Account Transfers</h2>
  <div class="sub abs">Vivamus porttitor purus nisi eleifend</div>
  <p class="copy abs">Morbi porta libero id ullamcorper nonummy nibh ligula pulvinar metus eget consectetuer augue nisi quis lacus Ut ac mi quis lacus mollis aliquam Curabitur iaculis tempus eros Curabitur vel mi sit amet magna malesuada ultrices Ut nisi erat fermentum vel congue id euismod in elit Fusce ultricies orci ac feugiat suscipit leo massa</p>
  <a class="btn-outline abs">Learn More</a>
  <div class="illus abs" role="img" aria-label="Illustration of hands exchanging a phone and a payment card"></div>
</section>

<section class="features abs">
  <div class="feature abs" style="left:183px">
    <svg class="icon" width="96" height="96" viewBox="0 0 96 96" role="img" aria-label="Secure payment icon">
      <path d="M30 10A42 42 0 1 0 66 10" fill="none" stroke="var(--cyan)" stroke-width="5" stroke-linecap="round"/>
      <path d="M48 46V12M48 12l-6 6M48 12l6 6M44 30L30 20M30 20v7M30 20h7M52 30l14-10M66 20v7M66 20h-7" fill="none" stroke="var(--cyan)" stroke-width="3" stroke-linecap="round" stroke-linejoin="round"/>
      <g transform="rotate(-18 52 62)">
        <rect x="30" y="48" width="44" height="26" rx="2" fill="var(--cyan)"/>
        <rect x="34" y="52" width="36" height="18" rx="1" fill="none" stroke="#fff" stroke-width="1.5"/>
        <circle cx="52" cy="61" r="5" fill="#fff"/>
      </g>
    </svg>
    <h3>Secure Payment</h3>
    <p>Donec dictum lectus non odio Cras a ante vitae enim iaculis aliquam Mauris nunc quam venenatis nec</p>
  </div>
  <div class="feature abs" style="left:472px">
    <svg class="icon" width="96" height="96" viewBox="0 0 96 96" role="img" aria-label="Payment cards icon">
      <path d="M22 20A42 42 0 1 0 74 20" fill="none" stroke="var(--cyan)" stroke-width="5" stroke-linecap="round"/>
      <g transform="rotate(-20 44 42)"><rect x="28" y="12" width="30" height="52" rx="3" fill="var(--cyan)"/><rect x="32" y="16" width="22" height="6" fill="#fff"/></g>
      <g transform="rotate(-8 56 50)"><rect x="44" y="20" width="30" height="52" rx="3" fill="var(--cyan)" stroke="#f2f2f2" stroke-width="2"/><rect x="48" y="26" width="22" height="6" fill="#fff"/></g>
    </svg>
    <h3>Easy to Send Money</h3>
    <p>Donec dictum lectus non odio Cras a ante vitae enim iaculis aliquam Mauris nunc quam venenatis nec</p>
  </div>
  <div class="feature abs" style="left:747px">
    <svg class="icon" width="96" height="96" viewBox="0 0 96 96" role="img" aria-label="Group of users icon">
      <path d="M8 48A40 40 0 0 0 88 48" fill="none" stroke="var(--cyan)" stroke-width="5" stroke-linecap="round"/>
      <circle cx="30" cy="30" r="7" fill="var(--cyan)"/><circle cx="66" cy="30" r="7" fill="var(--cyan)"/>
      <path d="M16 58c0-12 6-19 14-19s14 7 14 19z M52 58c0-12 6-19 14-19s14 7 14 19z" fill="var(--cyan)"/>
      <circle cx="48" cy="26" r="9" fill="var(--cyan)" stroke="#f2f2f2" stroke-width="2"/>
      <path d="M30 60c0-15 8-23 18-23s18 8 18 23z" fill="var(--cyan)" stroke="#f2f2f2" stroke-width="2"/>
    </svg>
    <h3>Million Users</h3>
    <p>Donec dictum lectus non odio Cras a ante vitae enim iaculis aliquam Mauris nunc quam venenatis nec</p>
  </div>
</section>

<div class="split-photo abs" role="img" aria-label="Photo of a woman sitting on a rug shopping on a laptop with a card"></div>
<section class="split-panel abs">
  <h2 class="abs">Send Money from Anywhere</h2>
  <div class="sub abs">Secure Money Transfer</div>
  <p class="copy abs">Morbi porta libero id ullamcorper nonummy nibh ligula pulvinar metus eget consectetuer augue nisi quis lacus<br>Ut ac mi quis lacus mollis aliquam Curabitur iaculis tempus eros Curabitur vel mi sit amet magna malesuada ultrices Ut nisi erat fermentumjusto id velit placerat molestie</p>
  <a class="btn-outline abs">Learn More</a>
</section>

<section class="clients abs">
  <h2 class="abs">Our Clients &amp; Partners</h2>
  <div class="client-row abs">
    <div class="client">Nerova <i class="round"></i></div>
    <div class="client">Pelmax</div>
    <div class="client">Urdo <i></i></div>
    <div class="client"><i></i> Kestra</div>
    <div class="client">Valto</div>
    <div class="client">Simbe</div>
  </div>
</section>

<section class="promo promo-how abs" role="img" aria-label="Photo of hands holding a tablet over papers, tinted grey">
  <h2>How it Works</h2>
  <p>Ut nisi erat fermentum vel congue id euismod in elit Fusce ultricies orci ac feugiat suscipit leo massa</p>
  <a class="btn-outline">Learn More</a>
</section>
<section class="promo promo-help abs" role="img" aria-label="Photo of a laptop keyboard, tinted yellow">
  <h2>Online Help &amp; Support</h2>
  <p>Ut nisi erat fermentum vel congue id euismod in elit Fusce ultricies orci ac feugiat suscipit leo massa</p>
  <a class="btn-outline">Learn More</a>
</section>

<section class="contact-bar abs">
  <div class="item abs" style="left:192px">Questions? Visit the Support Center, or get in touch:</div>
  <div class="item abs" style="left:500px;top:21px;font-size:14px">
    <svg width="20" height="20" viewBox="0 0 24 24"><path d="M6.6 10.8a15 15 0 0 0 6.6 6.6l2.2-2.2a1 1 0 0 1 1-.25 11 11 0 0 0 3.6.6 1 1 0 0 1 1 1V20a1 1 0 0 1-1 1A17 17 0 0 1 3 4a1 1 0 0 1 1-1h3.5a1 1 0 0 1 1 1c0 1.25.2 2.45.6 3.6a1 1 0 0 1-.25 1z" fill="none" stroke="#eee" stroke-width="1.8"/></svg>
    1-800-555-0147</div>
  <div class="item abs" style="left:672px">
    <svg width="22" height="16" viewBox="0 0 22 16"><rect x="1" y="1" width="20" height="14" rx="1.5" fill="#eee"/><path d="M1 2l10 7 10-7" fill="none" stroke="#333" stroke-width="1.6"/></svg>
    hello@fenwu-pay.eu</div>
  <div class="item abs" style="left:864px">
    <svg width="24" height="20" viewBox="0 0 24 20"><path d="M3 2h11a2 2 0 0 1 2 2v6a2 2 0 0 1-2 2H8l-4 3v-3H3a2 2 0 0 1-2-2V4a2 2 0 0 1 2-2z" fill="none" stroke="#eee" stroke-width="1.8"/><path d="M18 7h3a2 2 0 0 1 2 2v5a2 2 0 0 1-2 2v3l-4-3h-5" fill="none" stroke="#eee" stroke-width="1.8"/></svg>
    Live Chat</div>
</section>

<footer class="site-footer abs">
  <div class="foot-col abs" style="left:195px"><h4>COMPANY</h4><ul><li>Home</li><li>About Us</li><li>How it works</li><li>Features</li></ul></div>
  <div class="foot-col abs" style="left:379px"><h4>SERVICES</h4><ul><li>Online Transfer</li><li>Account to Account</li><li>Check Blanace</li><li>Status</li></ul></div>
  <div class="foot-col abs" style="left:581px"><h4>RESOURCES</h4><ul><li>Support</li><li>FAQ</li><li>Help</li><li>Contact</li></ul></div>
  <div class="foot-col abs" style="left:791px"><h4>WHY US</h4><ul><li>Ut nisi erat</li><li>Germentum vel</li><li>Congue euismod</li><li>Fusce ultricies</li></ul></div>
  <div class="foot-rule abs"></div>
  <div class="copyright abs">© 2016 Company Name &nbsp;All right reserved &nbsp;Term of Use</div>
  <div class="social abs" aria-label="Social links"><span></span><span></span><span></span><span></span></div>
</footer>

</body>
</html>
```